BOLD & MINIMALIST DESIGN NEEDED

We want a very bold but minimalistic business card design that is impactful and utilizes both sides of the business card. Our current logo is included for your use.

We want bold fonts and good use of negative space. We don't want the logo to overpower the design.

Target Market(s)

Professionals who are building new commercial buildings.

Industry/Entity Type

Construction

Contact Information for Business Card

Name, Title, email, office phone, cell phone, website

Font styles to use
Serif
Sans Serif

Requirements
Must have
• Bold design!

```html
<!DOCTYPE html>
<html lang="en">
<head>
<meta charset="utf-8">
<title>Ridgeline Design + Build — Business Card</title>
<link href="https://fonts.googleapis.com/css2?family=Montserrat:wght@400;500;700;800&display=swap" rel="stylesheet">
<style>
  :root {
    --stage: #2b2b2d;
    --card: #141414;
    --card-edge: #1f1f1f;
    --ink: #f2f2f2;
    --ink-soft: #d9d9d9;
    --accent: #7dc142;
    --emboss: #4d4d4f;
  }
  * { box-sizing: border-box; margin: 0; padding: 0; }
  html, body {
    width: 1200px; height: 874px; overflow: hidden;
    background: var(--stage);
    font-family: "Montserrat", Arial, sans-serif;
  }
  .stage {
    width: 1200px; height: 874px;
    display: flex; flex-direction: column; align-items: center; justify-content: center;
    gap: 46px;
  }
  .card {
    width: 640px; height: 366px;
    background: var(--card);
    border: 1px solid var(--card-edge);
    border-radius: 22px;
    box-shadow: 0 18px 40px rgba(0,0,0,.45);
    position: relative;
  }
  /* Front */
  .card--front { display: flex; align-items: center; justify-content: center; }
  .brand {
    display: flex; align-items: center; gap: 14px;
    font-weight: 800; text-transform: uppercase; letter-spacing: .02em; line-height: 1.05;
  }
  .brand__mark { width: 22px; height: 22px; flex: none; }
  .card--front .brand { color: var(--emboss); font-size: 40px; }
  .card--front .brand__mark { background: var(--emboss); width: 30px; height: 30px; }
  /* Back */
  .card--back { display: flex; align-items: center; }
  .back__brand { width: 300px; display: flex; justify-content: center; }
  .card--back .brand { color: var(--ink); font-size: 27px; }
  .card--back .brand__mark { background: var(--accent); }
  .divider { width: 2px; height: 210px; background: var(--accent); }
  .contact { padding-left: 28px; color: var(--ink-soft); }
  .contact__name { color: var(--accent); font-weight: 700; font-size: 27px; text-transform: uppercase; letter-spacing: .02em; }
  .contact__title { font-size: 14px; font-weight: 500; text-transform: uppercase; letter-spacing: .04em; margin-top: 2px; }
  .contact__address { font-size: 15px; line-height: 1.45; margin-top: 18px; }
  .contact__list { list-style: none; margin-top: 16px; font-size: 15px; line-height: 1.7; }
  .contact__list li { display: flex; align-items: center; gap: 10px; }
  .icon { width: 14px; height: 14px; fill: var(--accent); stroke: var(--accent); flex: none; }
</style>
</head>
<body>
<main class="stage">
  <section class="card card--front" aria-label="Card front">
    <div class="brand"><span class="brand__mark"></span><span>Ridgeline<br>Design + Build</span></div>
  </section>

  <section class="card card--back" aria-label="Card back">
    <div class="back__brand">
      <div class="brand"><span class="brand__mark"></span><span>Ridgeline<br>Design + Build</span></div>
    </div>
    <div class="divider"></div>
    <div class="contact">
      <h1 class="contact__name">Marcus Adeyemi</h1>
      <p class="contact__title">Owner-CEO</p>
      <p class="contact__address">48 Forge Lane, Millbrook<br>Ohio, Zip 4300</p>
      <ul class="contact__list">
        <li><svg class="icon" viewBox="0 0 16 16"><path stroke="none" d="M3 1h3l1.5 4-2 1.5a9 9 0 0 0 4 4L11 8.5 15 10v3a2 2 0 0 1-2 2A12 12 0 0 1 1 3a2 2 0 0 1 2-2z"/></svg>555 014 227</li>
        <li><svg class="icon" viewBox="0 0 16 16"><rect x="4" y="1" width="8" height="14" rx="1.5" fill="none" stroke-width="1.6"/><circle cx="8" cy="12.5" r="1" stroke="none"/></svg>555 014 228</li>
        <li><svg class="icon" viewBox="0 0 16 16"><rect x="1" y="3" width="14" height="10" rx="1" stroke="none"/><path d="M1.5 3.5 8 9l6.5-5.5" fill="none" stroke="#141414" stroke-width="1.4"/></svg>info@ridgelinebuild.com</li>
        <li><svg class="icon" viewBox="0 0 16 16"><circle cx="8" cy="8" r="6.5" fill="none" stroke-width="1.5"/><path d="M1.5 8h13M8 1.5c-3 3.5-3 9.5 0 13M8 1.5c3 3.5 3 9.5 0 13" fill="none" stroke-width="1.2"/></svg>www.ridgelinebuild.com</li>
      </ul>
    </div>
  </section>
</main>
</body>
</html>
```